Firm Stationery Design

I need a design for stationery, including: Stationery First Page, Stationery Second Sheet, Envelope, Mailing Label for Flat Envelopes, and Business Cards

```html
<!DOCTYPE html>
<html lang="en">
<head>
<meta charset="utf-8">
<title>Harlow Law LLC — Business Cards</title>
<link rel="stylesheet" href="https://fonts.googleapis.com/css2?family=Montserrat:wght@800&family=Arimo:wght@400;700&display=swap">
<style>
  :root {
    --backdrop: #3a3a3a;
    --card-front: #2d2d2d;
    --card-back: #1c1c1c;
    --orange: #ffa000;
    --white: #ffffff;
    --text-light: #f2f2f2;
  }
  * { box-sizing: border-box; margin: 0; padding: 0; }
  html, body { width: 1200px; height: 689px; overflow: hidden; }
  body {
    background: var(--backdrop);
    position: relative;
    font-family: "Arimo", Arial, sans-serif;
  }
  .card {
    position: absolute;
    top: 200px;
    width: 500px;
    height: 286px;
    border-radius: 16px;
    overflow: hidden;
  }
  .card-front { left: 60px; background: var(--card-front); }
  .card-back { left: 640px; background: var(--card-back); }

  /* Front */
  .front-brand {
    position: absolute;
    left: 0; right: 0; top: 96px;
    display: flex;
    flex-direction: column;
    align-items: center;
  }
  .brand-row { display: flex; align-items: center; gap: 14px; }
  .brand-square { width: 22px; height: 22px; background: var(--orange); }
  .brand-name {
    font-family: "Montserrat", Arial, sans-serif;
    font-weight: 800;
    font-size: 48px;
    letter-spacing: 1px;
    color: var(--white);
    line-height: 1;
  }
  .brand-sub {
    margin-top: 12px;
    font-family: "Montserrat", Arial, sans-serif;
    font-weight: 800;
    font-size: 14px;
    letter-spacing: 16px;
    color: var(--orange);
    padding-left: 16px;
  }

  /* Back */
  .back-bands { position: absolute; left: 0; top: 0; width: 250px; height: 286px; }
  .back-info {
    position: absolute;
    right: 28px; top: 28px;
    width: 210px;
    text-align: right;
    color: var(--text-light);
  }
  .back-info .brand-name { font-size: 34px; }
  .back-info .brand-sub { font-size: 10px; letter-spacing: 11px; margin-top: 6px; padding-left: 0; margin-right: -11px; }
  .person-name {
    margin-top: 18px;
    font-family: "Arimo", Arial, sans-serif;
    font-weight: 700;
    font-size: 20px;
    color: var(--orange);
    line-height: 1;
  }
  .person-title { font-size: 11px; margin-top: 4px; }
  .address { margin-top: 14px; font-size: 11px; line-height: 1.45; }
  .contacts { margin-top: 10px; list-style: none; font-size: 11px; line-height: 1.6; }
  .contacts li { display: flex; justify-content: flex-end; align-items: center; gap: 6px; }
  .contact-icon { width: 10px; height: 10px; fill: var(--orange); flex: none; }
</style>
</head>
<body>

<section class="card card-front" aria-label="Business card front">
  <div class="front-brand">
    <div class="brand-row">
      <span class="brand-square"></span>
      <span class="brand-name">HARLOW</span>
    </div>
    <div class="brand-sub">LAW LLC</div>
  </div>
</section>

<section class="card card-back" aria-label="Business card back">
  <svg class="back-bands" viewBox="0 0 250 286" aria-hidden="true">
    <rect x="0" y="0" width="250" height="286" fill="#1c1c1c"/>
    <rect x="120" y="0" width="22" height="286" fill="#ffffff"/>
    <rect x="150" y="0" width="58" height="286" fill="#ffa000"/>
  </svg>

  <div class="back-info">
    <div class="brand-name">HARLOW</div>
    <div class="brand-sub">LAW LLC</div>
    <div class="person-name">DANIEL REYES</div>
    <div class="person-title">President</div>
    <p class="address">412 Birchwood Road<br>Fairview, Canada 20418</p>
    <ul class="contacts">
      <li>555-210-4821
        <svg class="contact-icon" viewBox="0 0 10 10"><path d="M2 0.5 L3.8 2.6 L2.9 3.6 Q4 5.9 6.4 7.1 L7.4 6.2 L9.5 8 L8.3 9.5 Q1.2 8 0.5 1.7 Z"/></svg>
      </li>
      <li>555-318-7702
        <svg class="contact-icon" viewBox="0 0 10 10"><path d="M2.5 0 H7.5 V10 H2.5 Z M3.4 1 V8 H6.6 V1 Z"/></svg>
      </li>
      <li>info@harlowlaw.com
        <svg class="contact-icon" viewBox="0 0 10 10"><path d="M0 2 H10 V8.5 H0 Z M0.6 2.4 L5 5.6 L9.4 2.4 Z"/></svg>
      </li>
      <li>www.harlowlaw.com
        <svg class="contact-icon" viewBox="0 0 10 10"><circle cx="5" cy="5" r="4.8"/><path d="M1 5 H9 M5 0.5 V9.5" stroke="#1c1c1c" stroke-width="0.8"/></svg>
      </li>
    </ul>
  </div>
</section>

</body>
</html>
```